Business Card Design and Logo Needed

I need Business Cards and a Logo for my website and public speaking business which can be found at: www.corvina-lett.example

I'm looking for creative and unique ideas. Some business cards I've found online that I like can be found at:
http://gigbarrow.example/general/18-smokin-hot-business-card-designs/

and at

http://www.plumquarry.example/2009/04/50-creative-business-cards-of-50-graphic-designers/

```html
<!DOCTYPE html>
<html lang="en">
<head>
<meta charset="utf-8">
<title>Corvina Lett – Business Card</title>
<link rel="stylesheet" href="https://fonts.googleapis.com/css2?family=Architects+Daughter&family=Varela+Round&display=swap">
<style>
  :root {
    --backdrop: #000000;
    --card-top: #e4dead;
    --card-bottom: #d9d29c;
    --role-gold: #c4ad4c;
    --contact-grey: #4d4b3f;
    --mark-dark: #2e2b1c;
  }
  html, body {
    margin: 0;
    padding: 0;
    width: 1012px;
    height: 1200px;
    overflow: hidden;
    background: var(--backdrop);
  }
  .canvas {
    position: relative;
    width: 1012px;
    height: 1200px;
  }
  .card-shape {
    position: absolute;
    inset: 0;
  }
  .roles {
    position: absolute;
    left: 237px;
    top: 298px;
    margin: 0;
    padding: 0;
    list-style: none;
    font-family: "Architects Daughter", cursive;
    font-size: 54px;
    line-height: 82px;
    color: var(--role-gold);
  }
  .contact {
    position: absolute;
    right: 217px;
    top: 578px;
    margin: 0;
    text-align: right;
    font-family: "Varela Round", sans-serif;
    font-style: normal;
    font-weight: 700;
    font-size: 34px;
    line-height: 49px;
    color: var(--contact-grey);
    letter-spacing: 0.5px;
  }
  .contact span { display: block; }
  .brand {
    position: absolute;
    left: 419px;
    top: 830px;
    width: 226px;
    display: flex;
    flex-direction: column;
    align-items: center;
    gap: 18px;
  }
  .brand-dot {
    width: 130px;
    height: 130px;
    border-radius: 50%;
    background: var(--mark-dark);
  }
  .brand-name {
    font-family: "Varela Round", sans-serif;
    font-weight: 400;
    font-size: 34px;
    color: var(--contact-grey);
    white-space: nowrap;
  }
</style>
</head>
<body>
<main class="canvas">
  <svg class="card-shape" width="1012" height="1200" viewBox="0 0 1012 1200" aria-hidden="true">
    <defs>
      <linearGradient id="card-fill" x1="0" y1="0" x2="0" y2="1">
        <stop offset="0" stop-color="var(--card-top)"/>
        <stop offset="1" stop-color="var(--card-bottom)"/>
      </linearGradient>
    </defs>
    <path fill="url(#card-fill)"
      d="M268 150 H700 C694 185 716 232 762 240 L790 244 Q818 248 818 278 V1070 Q818 1118 770 1118 H268 Q220 1118 220 1070 V198 Q220 150 268 150 Z"/>
  </svg>

  <ul class="roles">
    <li>Motivational Speaker</li>
    <li>Philanthropist</li>
    <li>Author</li>
  </ul>

  <address class="contact">
    <span class="contact-phone">mob : 0100 555 012</span>
    <span class="contact-web">www.corvina-lett.example</span>
    <span class="contact-email">corvinalett@mailbox.example</span>
  </address>

  <div class="brand">
    <div class="brand-dot"></div>
    <div class="brand-name">Corvina Lett</div>
  </div>
</main>
</body>
</html>
```